Construction company business card

One side to be the logo with the company name, The other side I would like: (Tomas verbick) Project manager 41 barrow crescent kelbrook 52917306224783(03) 9703 2428Info@gudeljgroup.comAnd then maybe a couple dot points saying what we do:Construction (commercial & industrial) Civil construction

Anything else please contact me!
Maybe curved st one edge of the card

Target Market(s)

Older clientele

Industry/Entity Type

Construction Company

Contact Information for Business Card

Read above

Colors
3277b5
1b1b1b
9d9d9d

Requirements
Must have
• Use my logo on one side
Nice to have
• Read above
Should not have
• Read above

```html
<!DOCTYPE html>
<html lang="en">
<head>
<meta charset="utf-8">
<title>Stonebay Property Group – Business Card</title>
<link rel="stylesheet" href="https://fonts.googleapis.com/css2?family=Open+Sans:wght@400;700;800&display=swap">
<style>
  :root {
    --brand-blue: #3277b5;
    --ink: #1b1b1b;
    --stone-grey: #9d9d9d;
    --text-grey: #5a5a5a;
    --paper: #ffffff;
    --backdrop: #2b2b2b;
  }
  * { box-sizing: border-box; margin: 0; padding: 0; }
  html, body {
    width: 1200px; height: 866px; overflow: hidden;
    background: var(--backdrop);
    font-family: "Open Sans", Arial, sans-serif;
  }
  .card-set {
    position: absolute; inset: 0;
    display: flex; align-items: center; justify-content: center; gap: 40px;
  }
  .card {
    width: 540px; height: 309px; position: relative; overflow: hidden;
    box-shadow: 0 10px 24px rgba(0,0,0,.45);
  }

  /* Front: logo side */
  .card--front {
    background: var(--brand-blue);
    display: flex; align-items: center; justify-content: center;
  }
  .brand {
    display: flex; align-items: center; gap: 14px;
  }
  .brand__dot {
    width: 22px; height: 22px; border-radius: 50%; flex: none;
  }
  .brand__name {
    font-weight: 800; letter-spacing: .02em; line-height: 1.05;
    text-transform: uppercase; white-space: nowrap;
  }
  .brand__name small {
    display: block; font-size: .42em; letter-spacing: .32em;
  }
  .card--front .brand__dot { background: var(--paper); }
  .card--front .brand__name { color: var(--paper); font-size: 44px; }

  /* Back: contact side */
  .card--back {
    background: var(--paper);
    border-bottom: 8px solid var(--brand-blue);
    padding: 40px 36px 0 40px;
  }
  .contact__name {
    color: var(--brand-blue); font-weight: 700; font-size: 21px;
    text-transform: uppercase; letter-spacing: .01em;
  }
  .contact__role { color: var(--text-grey); font-size: 14px; margin-bottom: 6px; }
  .contact__list { list-style: none; color: var(--text-grey); font-size: 13.5px; line-height: 1.5; }
  .contact__list li { display: flex; align-items: center; gap: 6px; }
  .contact__list svg { width: 11px; height: 11px; fill: var(--brand-blue); flex: none; }
  .contact__list .contact__address { margin-top: 4px; }

  .card--back .brand {
    position: absolute; right: 40px; top: 112px;
  }
  .card--back .brand__dot { background: var(--brand-blue); width: 18px; height: 18px; }
  .card--back .brand__name { color: var(--brand-blue); font-size: 30px; }

  .services {
    position: absolute; right: 40px; bottom: 30px;
    list-style: none; text-align: right;
    color: var(--text-grey); font-size: 14px; line-height: 1.4;
  }
  .services li::after {
    content: ""; display: inline-block; width: 8px; height: 8px; margin-left: 7px;
    border-radius: 50%; background: var(--brand-blue); vertical-align: middle;
  }
  .services li.services__note::after { content: none; }
  .services li.services__note { margin-right: 15px; }
</style>
</head>
<body>
<main class="card-set">
  <section class="card card--front" aria-label="Card front">
    <div class="brand">
      <span class="brand__dot"></span>
      <span class="brand__name">Stonebay<small>Property Group</small></span>
    </div>
  </section>

  <section class="card card--back" aria-label="Card back">
    <h1 class="contact__name">Tomas Verbick</h1>
    <p class="contact__role">Project manager</p>
    <ul class="contact__list">
      <li>
        <svg viewBox="0 0 12 12" aria-hidden="true"><path d="M1 4c0-2 2-3 5-3s5 1 5 3l-2 1-1-1.5H4L3 5zM3 6h6l1.5 5h-9z"/></svg>
        7306224783
      </li>
      <li>
        <svg viewBox="0 0 12 12" aria-hidden="true"><path d="M3 0h6a1 1 0 0 1 1 1v10a1 1 0 0 1-1 1H3a1 1 0 0 1-1-1V1a1 1 0 0 1 1-1zm.5 1.5v8h5v-8z"/></svg>
        (03) 9418 6573
      </li>
      <li>
        <svg viewBox="0 0 12 12" aria-hidden="true"><path d="M0 2h12v8H0zm1 1v.4l5 3.2 5-3.2V3z"/></svg>
        Info@verbickgroup.com
      </li>
      <li class="contact__address">41 barrow crescent kelbrook 5291</li>
    </ul>

    <div class="brand">
      <span class="brand__dot"></span>
      <span class="brand__name">Stonebay<small>Property Group</small></span>
    </div>

    <ul class="services">
      <li>Construction</li>
      <li class="services__note">(commercial &amp; industrial)</li>
      <li>Civil construction</li>
    </ul>
  </section>
</main>
</body>
</html>
```